BrindleStaffing Business Card Design

We are a staffing company finding positions for dedicated nurses and physicians.

Target Market(s)

Business Professionals

Industry/Entity Type

Staffing

Contact Information for Business Card

Gordon Pratley
Chairman
417 39th Avenue South
SAINT PETERSBURG FL 33712
813-555-4172 Mobile
813-555-8036 Fax
gpratley@brindlestaffing.com
www.brindlestaffing.com

Font styles to use
Sans Serif

Colors
fbee3e
f04a50
f37122

Requirements
Must have
• Logo Attached, see colors below. We'd like to see Yellow, Orange and Red.

```html
<!DOCTYPE html>
<html lang="en">
<head>
<meta charset="utf-8">
<title>BrindleStaffing Business Card</title>
<link rel="stylesheet" href="https://fonts.googleapis.com/css2?family=Quicksand:wght@400;500;700&display=swap">
<style>
  :root {
    --backdrop: #2b2b2b;
    --brand-yellow: #fbee3e;
    --brand-orange: #f37122;
    --brand-red: #f04a50;
    --ink: #444444;
    --card-white: #ffffff;
  }
  * { box-sizing: border-box; margin: 0; padding: 0; }
  html, body { width: 1200px; height: 1108px; overflow: hidden; }
  body {
    background: var(--backdrop);
    font-family: "Quicksand", sans-serif;
    position: relative;
  }
  .card {
    position: absolute;
    left: 250px;
    width: 700px;
    height: 400px;
    box-shadow: 0 12px 30px rgba(0,0,0,0.45);
    overflow: hidden;
  }
  .card--back { top: 114px; background: var(--brand-orange); }
  .card--front { top: 594px; background: var(--card-white); }

  .card__pattern {
    position: absolute; inset: 0;
    background: radial-gradient(circle at 50% 50%, #f69a3a 0%, var(--brand-orange) 75%);
  }
  .back__wordmark {
    position: absolute; left: 0; right: 0; top: 150px;
    text-align: center;
    font-weight: 700; font-size: 58px; letter-spacing: -1.5px;
    color: var(--card-white);
  }
  .back__web {
    position: absolute; left: 0; right: 0; top: 262px;
    text-align: center;
    font-size: 15px; letter-spacing: 7px;
    color: var(--card-white);
  }

  .front__wordmark {
    position: absolute; left: 270px; top: 62px;
    font-weight: 700; font-size: 56px; letter-spacing: -1.5px;
    color: var(--brand-orange);
  }
  .front__wordmark-dot {
    display: inline-block; width: 14px; height: 14px; border-radius: 50%;
    background: var(--brand-yellow); margin-left: 6px; vertical-align: middle;
  }
  .front__rule-accent {
    position: absolute; left: 40px; top: 168px; width: 190px; height: 4px;
    background: var(--brand-orange);
  }
  .front__rule-line {
    position: absolute; left: 230px; top: 170px; width: 420px; height: 1px;
    background: var(--brand-red);
  }
  .person { position: absolute; left: 40px; top: 182px; }
  .person__name { font-size: 27px; font-weight: 500; color: var(--brand-red); line-height: 1.1; }
  .person__title { font-size: 15px; color: var(--brand-orange); margin-bottom: 10px; }
  .person__address { font-size: 15px; color: var(--ink); line-height: 1.45; }

  .contact {
    position: absolute; right: 40px; top: 258px;
    list-style: none;
    font-size: 17px; color: var(--ink);
  }
  .contact__item {
    display: flex; justify-content: flex-end; align-items: center;
    gap: 10px; height: 27px;
  }
  .contact__icon { width: 18px; height: 18px; flex: none; }
</style>
</head>
<body>
  <section class="card card--back" aria-label="Card back">
    <div class="card__pattern" role="img" aria-label="Soft dotted orange background pattern"></div>
    <div class="back__wordmark">BrindleStaffing</div>
    <div class="back__web">www.brindlestaffing.com</div>
  </section>

  <section class="card card--front" aria-label="Card front">
    <div class="front__wordmark">BrindleStaffing<span class="front__wordmark-dot"></span></div>
    <div class="front__rule-accent"></div>
    <div class="front__rule-line"></div>

    <div class="person">
      <p class="person__name">Gordon Pratley</p>
      <p class="person__title">Chairman</p>
      <p class="person__address">417 39th Avenue South<br>SAINT PETERSBURG FL 33712</p>
    </div>

    <ul class="contact">
      <li class="contact__item">813-555-4172
        <svg class="contact__icon" viewBox="0 0 18 18"><rect x="4" y="1" width="10" height="16" rx="2" fill="none" stroke="var(--brand-red)" stroke-width="2"/></svg>
      </li>
      <li class="contact__item">813-555-8036
        <svg class="contact__icon" viewBox="0 0 18 18"><rect x="5" y="1" width="8" height="5" fill="var(--brand-red)"/><rect x="1" y="7" width="16" height="7" rx="1.5" fill="var(--brand-red)"/><rect x="5" y="12" width="8" height="5" fill="none" stroke="var(--brand-red)" stroke-width="1.5"/></svg>
      </li>
      <li class="contact__item">gpratley@brindlestaffing.com
        <svg class="contact__icon" viewBox="0 0 18 18"><rect x="1" y="4" width="16" height="11" fill="var(--brand-red)"/><path d="M1 4 L9 11 L17 4" fill="none" stroke="#fff" stroke-width="1.5"/></svg>
      </li>
      <li class="contact__item">www.brindlestaffing.com
        <svg class="contact__icon" viewBox="0 0 18 18"><circle cx="9" cy="9" r="8" fill="var(--brand-red)"/><path d="M1 9 H17 M9 1 C5 5 5 13 9 17 M9 1 C13 5 13 13 9 17" fill="none" stroke="#fff" stroke-width="1.2"/></svg>
      </li>
    </ul>
  </section>
</body>
</html>
```